Upmarket Dessert Lounge needs a Business Card Design

We are an upmarket dessert lounge needing a business card to match our image.

We want something that is simple yet beautiful, feminine, classy, sophisticated and elegant. We want it to stand out and don't mind if it is bold.

The design should include our logo and colours of red or maroon with gold highlights. We don't mind if black is used.

Marlow & Quince

Target Market(s)

For those who like to indulge or treat themselves and give in to their temptations on good quality desserts.

Industry/Entity Type

Business

Requirements
Must have
• Must include our logo and our name

Marlow & Quince

M & Q

```html
<!DOCTYPE html>
<html lang="en">
<head>
<meta charset="utf-8">
<title>Marlow &amp; Quince — Business Card</title>
<link href="https://fonts.googleapis.com/css2?family=Open+Sans:wght@400;600&display=swap" rel="stylesheet">
<style>
  :root {
    --backdrop: #e9e6e2;
    --card: #ffffff;
    --maroon: #7a1e1e;
    --maroon-deep: #5c1212;
    --maroon-bright: #b3261e;
    --gold: #e8b878;
    --gold-soft: #f6e1c0;
    --ink: #2b2b2b;
  }
  * { margin: 0; padding: 0; box-sizing: border-box; }
  html, body { width: 1200px; height: 951px; overflow: hidden; }
  body {
    background: var(--backdrop);
    font-family: "Open Sans", Arial, sans-serif;
    position: relative;
  }
  .card {
    position: absolute;
    width: 560px;
    height: 320px;
    background: var(--card);
    border-radius: 26px;
    overflow: hidden;
    box-shadow: 0 8px 24px rgba(0,0,0,0.18);
  }
  .card--front { left: 90px; top: 120px; }
  .card--back { left: 550px; top: 510px; }

  .corner-ornament {
    position: absolute;
    right: 0; top: 0;
    width: 320px; height: 96px;
  }
  .corner-ornament svg { display: block; width: 100%; height: 100%; }

  .brand {
    position: absolute;
    display: flex;
    align-items: center;
    gap: 12px;
    white-space: nowrap;
  }
  .brand__dot {
    flex: none;
    border-radius: 50%;
    background: var(--maroon);
  }
  .brand__name {
    color: var(--maroon);
    font-weight: 600;
    letter-spacing: 0.04em;
  }
  .card--front .brand { left: 0; right: 0; top: 126px; justify-content: center; }
  .card--front .brand__dot { width: 18px; height: 18px; }
  .card--front .brand__name { font-size: 32px; }
  .card--front .website {
    position: absolute;
    left: 0; right: 0; bottom: 40px;
    text-align: center;
    font-size: 17px;
    letter-spacing: 0.08em;
    color: var(--ink);
  }

  .card--back .brand { left: 36px; top: 114px; gap: 9px; }
  .card--back .brand__dot { width: 14px; height: 14px; }
  .card--back .brand__name { font-size: 23px; }
  .contact {
    position: absolute;
    left: 340px; top: 84px;
    color: var(--ink);
  }
  .contact__name {
    font-size: 20px;
    color: var(--maroon);
    margin-bottom: 22px;
  }
  .contact__list { list-style: none; font-size: 15px; line-height: 19px; }
  .contact__list li { display: flex; align-items: center; gap: 8px; }
  .contact__list svg { width: 13px; height: 13px; flex: none; }
  .contact__list .accent { color: var(--maroon); }

  .base-line {
    position: absolute;
    left: 0; right: 0; bottom: 40px;
    height: 3px;
    background: var(--gold);
  }
  .base-band {
    position: absolute;
    left: 0; right: 0; bottom: 0;
    height: 36px;
    background: linear-gradient(180deg, var(--maroon-bright), var(--maroon-deep));
  }
</style>
</head>
<body>
  <section class="card card--front">
    <div class="corner-ornament" role="img" aria-label="Gold floral flourish ornament in the top corner">
      <svg viewBox="0 0 320 96" preserveAspectRatio="none">
        <defs>
          <linearGradient id="ornamentTone" x1="0" y1="0" x2="1" y2="1">
            <stop offset="0" stop-color="#f6e1c0"/>
            <stop offset="1" stop-color="#e8b878"/>
          </linearGradient>
        </defs>
        <path d="M0 0 H320 V96 C260 70 190 66 120 44 C70 28 30 16 0 0 Z" fill="url(#ornamentTone)" opacity="0.85"/>
      </svg>
    </div>
    <div class="brand">
      <span class="brand__dot"></span>
      <span class="brand__name">Marlow &amp; Quince</span>
    </div>
    <p class="website">www.marlowquince.com</p>
  </section>

  <section class="card card--back">
    <div class="brand">
      <span class="brand__dot"></span>
      <span class="brand__name">Marlow &amp; Quince</span>
    </div>
    <div class="contact">
      <p class="contact__name">Marlow &amp; Quince</p>
      <ul class="contact__list">
        <li>
          <svg viewBox="0 0 16 16"><path fill="#7a1e1e" d="M4 1l3 3-2 2c1 2 3 4 5 5l2-2 3 3-2 3C7 15 1 9 1 3z"/></svg>
          512-555-0140
        </li>
        <li>
          <svg viewBox="0 0 16 16"><rect x="4" y="1" width="8" height="14" rx="2" fill="#7a1e1e"/><rect x="6" y="3" width="4" height="8" fill="#fff"/></svg>
          512-555-0141
        </li>
        <li>
          <svg viewBox="0 0 16 16"><rect x="1" y="3" width="14" height="10" rx="1" fill="#7a1e1e"/><path d="M1 4l7 5 7-5" stroke="#fff" stroke-width="1.4" fill="none"/></svg>
          info@marlowquince.com
        </li>
        <li>
          <svg viewBox="0 0 16 16"><circle cx="8" cy="8" r="7" fill="#7a1e1e"/></svg>
          <span>www.<span class="accent">marlowquince</span>.com</span>
        </li>
      </ul>
    </div>
    <div class="base-line"></div>
    <div class="base-band"></div>
  </section>
</body>
</html>
```